Machinery Harbor Corp - Business Card Design

Need a new modern designed business card that is different and stands out to represent my equipment financing company. Machinery Harbor Corp finances all types of equipment and all types of industries. We like to do equipment financing a different way by putting customers first and want our card to represent that different approach to business. I want a card that some remembers when they receive it so it sticks in their mind and makes that wow impression.

Card should have a black background so the logo stands out. It can be horizontial or vertical or a combination of both.

Front of card information is below that shows the information that would go on my card. That is where I want a different look or design to stand out. The front could be split black/orange colour so the logo could pop on black side and information on orange side with different lettering. Just outside the box thinking on the front of the card. Open to any type of design.

Back of card is below which i I like unless you have a different spin to provide or a different idea that would make the card better as I am open to anything that looks great.

Target Market(s)

Machinery Harbor Corp deals with business owners in all industries.

Industry/Entity Type

Business

Contact Information for Business Card

Colors

Designer to choose colors to be used in the design.

Requirements
Must have
• Modern
• Different
• Stand Out
• Makes an Impression

```html
<!DOCTYPE html>
<html lang="en">
<head>
<meta charset="utf-8">
<title>Machinery Harbor Corp – Business Card</title>
<link href="https://fonts.googleapis.com/css2?family=Lato:wght@400;700&display=swap" rel="stylesheet">
<style>
  :root {
    --backdrop: #3b3026;
    --card-black: #000000;
    --orange-deep: #f15a22;
    --orange-bright: #f7931e;
    --brand-orange: #f26b21;
    --text-white: #ffffff;
    --stripe-text: #1a0d05;
  }
  html, body {
    margin: 0;
    padding: 0;
    width: 1189px;
    height: 1200px;
    overflow: hidden;
    background: var(--backdrop);
    font-family: "Lato", Arial, sans-serif;
  }
  .canvas {
    position: relative;
    width: 1189px;
    height: 1200px;
  }
  .card {
    position: absolute;
    top: 233px;
    width: 436px;
    height: 764px;
    background: var(--card-black);
    overflow: hidden;
    box-shadow: 0 6px 18px rgba(0,0,0,0.45);
  }
  .card--back {
    left: 121px;
    border-radius: 0 38px 0 38px;
  }
  .card--front {
    left: 624px;
    border-radius: 38px 0 38px 0;
  }
  .web-stripe {
    position: absolute;
    top: 0;
    left: 26px;
    width: 37px;
    height: 100%;
    background: linear-gradient(90deg, var(--orange-deep), var(--orange-bright));
  }
  .web-stripe__url {
    position: absolute;
    top: 76px;
    left: 50%;
    transform: translateX(-50%);
    writing-mode: vertical-rl;
    text-orientation: upright;
    font-size: 15px;
    letter-spacing: 4.5px;
    color: var(--stripe-text);
    line-height: 1;
  }
  .brand {
    position: absolute;
    display: flex;
    align-items: center;
    gap: 10px;
    color: var(--brand-orange);
    font-weight: 400;
    text-transform: uppercase;
    white-space: nowrap;
  }
  .brand__dot {
    width: 12px;
    height: 12px;
    border-radius: 50%;
    background: var(--brand-orange);
    flex: none;
  }
  .brand__name {
    text-align: center;
    line-height: 1.2;
  }
  .card--back .brand {
    right: 44px;
    top: 672px;
    font-size: 20px;
    letter-spacing: 2px;
  }
  .card--front .brand {
    left: 63px;
    right: 0;
    justify-content: center;
    top: 250px;
    font-size: 24px;
    letter-spacing: 2.5px;
  }
  .person {
    position: absolute;
    left: 87px;
    top: 481px;
    color: var(--text-white);
  }
  .person__name {
    margin: 0;
    font-size: 26px;
    font-weight: 700;
    line-height: 1.1;
  }
  .person__title {
    margin: 2px 0 0;
    font-size: 20px;
    font-weight: 400;
  }
  .contact {
    position: absolute;
    left: 87px;
    top: 640px;
    margin: 0;
    color: var(--text-white);
    font-size: 19px;
    line-height: 1.4;
  }
</style>
</head>
<body>
<main class="canvas">
  <section class="card card--back" aria-label="Card back">
    <div class="web-stripe"><span class="web-stripe__url">www.machineryharborcorp.ca</span></div>
    <div class="brand"><span class="brand__dot"></span><span class="brand__name">Machinery Harbor<br>Corp</span></div>
  </section>

  <section class="card card--front" aria-label="Card front">
    <div class="web-stripe"><span class="web-stripe__url">www.machineryharborcorp.ca</span></div>
    <div class="brand"><span class="brand__dot"></span><span class="brand__name">Machinery Harbor<br>Corp</span></div>
    <div class="person">
      <p class="person__name">DEAN MARLOW</p>
      <p class="person__title">PRESIDENT</p>
    </div>
    <p class="contact">587.204.3196<br>dean@machineryharborcorp.ca</p>
  </section>
</main>
</body>
</html>
```